Merry Meadow Roasters

We need a website to sell coffee with a horse theme. We already have a logo and have designed 4 different coffee bags/flavors so far, each of which will be available in ground or whole bean. The brand is intended to be light hearted/whimsical.

Requirements
Must have
• incorporation of attached photos
Nice to have
• underlying background theme with sky/grass

```html
<!DOCTYPE html>
<html lang="en">
<head>
<meta charset="utf-8">
<title>Merry Meadow Roasters</title>
<link href="https://fonts.googleapis.com/css2?family=Bungee&family=Montserrat:wght@400;500;600;700&display=swap" rel="stylesheet">
<style>
:root{
  --orange:#d2601a;
  --orange-dark:#b9500f;
  --brown:#3a1a10;
  --brown-mid:#4a2416;
  --peach:#fcece0;
  --ink:#1f1f1f;
  --text:#555;
  --white:#fff;
  --line:#b9b9b9;
}
*{box-sizing:border-box;margin:0;padding:0}
html,body{width:1200px;height:3936px;overflow:hidden}
body{position:relative;background:var(--white);font-family:"Montserrat",sans-serif;color:var(--ink)}
.abs{position:absolute}
.display{font-family:"Bungee",sans-serif;letter-spacing:2px;color:var(--ink)}
.btn{position:absolute;display:flex;align-items:center;justify-content:center;border-radius:30px;font-weight:600;font-size:13px;text-transform:uppercase;color:var(--white);background:var(--orange)}
.rule{position:absolute;width:30px;height:3px;background:var(--orange)}

/* hero */
.hero-photo{left:0;top:0;width:1200px;height:720px;background:linear-gradient(180deg,#eae7df 0%,#ead7a8 18%,#dea25a 30%,#8f8a3e 45%,#5e6a2b 65%,#4f5c25 100%)}
.logo{left:145px;top:40px;width:160px;display:flex;flex-direction:column;align-items:center;gap:8px}
.logo-dot{width:52px;height:52px;border-radius:50%;background:var(--white)}
.logo-name{font-weight:700;font-size:18px;line-height:1.1;text-align:center;color:var(--brown)}
.search{left:803px;top:21px;width:176px;height:31px;border:1px solid #999;border-radius:16px;background:#f4f4f4;font-size:11px;color:#555;padding:8px 14px}
.search-btn{right:3px;top:3px;width:23px;height:23px;border-radius:50%;background:var(--orange)}
.nav{left:566px;top:78px;display:flex;gap:27px;font-weight:600;font-size:13.5px}
.nav a{color:var(--ink);text-decoration:none;position:relative}
.nav a.active::after{content:"";position:absolute;left:8px;right:8px;top:20px;height:3px;border-radius:3px;background:var(--orange)}
.cart{left:1014px;top:68px;width:36px;height:36px;border-radius:50%;background:var(--white);display:flex;align-items:center;justify-content:center}
.cart-count{right:-6px;top:-4px;width:15px;height:15px;border-radius:50%;background:var(--orange);color:#fff;font-size:9px;display:flex;align-items:center;justify-content:center}
.headline{left:142px;top:368px;font-size:40px;line-height:54px;color:var(--white)}
.btn-ghost{background:var(--white);color:var(--ink)}
.hero-ring{left:638px;top:275px;width:460px;height:460px;border-radius:50%;background:rgba(255,255,255,.25)}
.hero-circle{left:662px;top:300px;width:412px;height:412px;border-radius:50%;background:linear-gradient(160deg,#e6d9c8,#c9b6a0 70%,#6a4a35)}

/* products */
.products-bg{left:0;top:1300px;width:1200px;height:870px;background:linear-gradient(180deg,#f6f3ee 0%,#dfe3e6 25%,#c7c9c4 45%,#8b6c50 62%,#4a3526 80%,#6b4a2c 100%)}
.card{position:absolute;width:439px;height:341px;border:1.5px solid var(--line);background:var(--white)}
.card.left{border-radius:70px 0 0 70px}
.card.right{border-radius:0 70px 70px 0}
.card.peach{background:var(--peach)}
.bag{position:absolute;left:46px;top:56px;width:170px;height:236px;border-radius:8px 8px 4px 4px;background:linear-gradient(180deg,#c99b6b,#b58456)}
.card h3{position:absolute;left:250px;top:56px;font-size:15px;font-weight:600}
.card p{position:absolute;left:250px;top:90px;width:170px;font-size:13.5px;line-height:21.5px;color:var(--text)}
.price{position:absolute;left:250px;top:194px;font-size:18px;font-weight:600;color:#444}
.stars{position:absolute;left:337px;top:192px;font-size:16px;color:var(--orange);letter-spacing:-1px}
.card .btn{left:250px;top:240px;width:136px;height:40px;font-size:11px;justify-content:flex-start;padding-left:24px}
.btn-icon{position:absolute;right:5px;top:5px;width:30px;height:30px;border-radius:50%;background:#fff;display:flex;align-items:center;justify-content:center}
.medallion{left:540px;top:1232px;width:120px;height:120px;border-radius:50%;background:var(--white)}
.medallion span{position:absolute;left:30px;top:30px;width:60px;height:60px;border-radius:50%;background:#efe3d6}

/* about */
.about-bg{left:0;top:2100px;width:1200px;height:660px;background:var(--peach)}
.coffee-photo{left:0;top:2200px;width:595px;height:520px;background:radial-gradient(circle at 48% 45%,#8a4d2a 0 24%,#b87a4e 25% 30%,transparent 31%),radial-gradient(ellipse at 30% 60%,#3d1d10 0,#5a2c17 40%,rgba(90,44,23,0) 70%)}
.about-title{left:618px;top:2196px;font-size:38px}
.about-text{left:618px;top:2284px;width:435px;font-size:15px;line-height:27.3px;color:var(--text);text-align:justify}

/* blog */
.blog-title{left:0;width:1200px;top:2690px;font-size:38px;text-align:center}
.post{position:absolute;width:296px}
.post-img{width:100%;height:179px}
.date{position:absolute;left:16px;top:162px;background:#5a4a40;color:#fff;font-size:14px;padding:6px 12px}
.post h4{margin:40px 6px 0;font-size:13px;font-weight:600}
.post p{margin:10px 6px 0;font-size:12.5px;line-height:21px;color:#777}
.post a{display:block;margin:18px 6px 0;font-size:12.5px;font-weight:600;color:var(--orange)}
.meadow{left:0;top:3060px;width:1200px;height:400px;background:linear-gradient(180deg,rgba(255,255,255,0) 0%,#dfe4d8 20%,#8aa066 50%,#6b8745 75%,#5d7a3b 100%)}

/* footer */
.footer{left:0;top:3400px;width:1200px;height:536px;background:var(--brown)}
.subscribe{left:179px;top:3494px;width:842px;height:107px;background:var(--brown-mid)}
.subscribe h5{position:absolute;left:32px;top:40px;font-size:21px;font-weight:600;color:#fff}
.email{position:absolute;left:311px;top:33px;width:370px;height:41px;border-radius:22px;background:#fff;font-size:13px;color:#444;padding:13px 28px}
.subscribe .btn{left:688px;top:33px;width:121px;height:41px}
.fcol{position:absolute;top:3645px;border-left:2px solid var(--orange);padding-left:12px;height:150px;color:#fff}
.fcol h6{font-size:14px;font-weight:600;margin-bottom:14px}
.fcol li{list-style:none;font-size:13px;line-height:32px}
.contact-item{display:flex;gap:14px;font-size:13px;line-height:21px}
.bottom-line{left:0;top:3830px;width:1200px;height:1px;background:rgba(255,255,255,.2)}
.legal{left:145px;top:3878px;font-size:12.5px;color:#fff}
.cards{left:705px;top:3874px;display:flex;gap:9px}
.cards span{width:28px;height:19px;border-radius:3px;background:#e2e2e2}
.social{left:924px;top:3871px;display:flex;gap:9px}
.social span{width:26px;height:26px;border-radius:50%;border:2px solid #fff}
</style>
</head>
<body>

<!-- HERO -->
<div class="abs hero-photo" role="img" aria-label="Horses grazing in a sunlit grassy pasture at sunset"></div>
<svg class="abs" style="left:0;top:540px" width="1200" height="200" viewBox="0 0 1200 200">
  <path d="M0 80 C160 150 330 160 520 100 C700 45 900 70 1200 40 L1200 200 L0 200 Z" fill="#fff"/>
  <path d="M200 163 C360 180 520 150 690 40" fill="none" stroke="#d2601a" stroke-width="7" stroke-linecap="round"/>
</svg>
<div class="abs hero-ring"></div>
<div class="abs hero-circle" role="img" aria-label="Coffee bag of whole beans on a scattering of beans"></div>

<div class="abs logo"><span class="logo-dot"></span><span class="logo-name">Merry Meadow Roasters</span></div>
<div class="abs search">Search<span class="abs search-btn"></span></div>
<nav class="abs nav"><a class="active">HOME</a><a>SHOP</a><a>ABOUT US</a><a>BLOG</a><a>CONTACT US</a></nav>
<div class="abs cart">
  <svg width="20" height="18" viewBox="0 0 20 18"><path d="M1 2h3l2.5 9h10l2-7H5.5" fill="#111" stroke="#111" stroke-width="1.6" stroke-linejoin="round"/><circle cx="8" cy="15" r="1.7" fill="#111"/><circle cx="15" cy="15" r="1.7" fill="#111"/></svg>
  <span class="abs cart-count">0</span>
</div>
<h1 class="abs display headline">GIDDY UP &amp; GET<br>CAFFEINATED!</h1>
<a class="btn" style="left:142px;top:497px;width:184px;height:54px">SHOP PRODUCTS</a>
<a class="btn btn-ghost" style="left:335px;top:497px;width:184px;height:54px">CONTACT US</a>

<!-- FEATURED -->
<h2 class="abs display" style="left:0;width:1200px;top:806px;font-size:38px;text-align:center">FEATURED PRODUCTS</h2>
<span class="rule" style="left:585px;top:868px"></span>

<div class="abs products-bg" role="img" aria-label="Hazy sky above a herd of horses galloping across a field"></div>
<svg class="abs" style="left:0;top:1990px" width="1200" height="180" viewBox="0 0 1200 180">
  <path d="M0 110 C250 200 450 120 640 50 C850 -20 1050 40 1200 100 L1200 180 L0 180 Z" fill="#fff"/>
  <path d="M0 125 C250 210 450 135 640 65 C850 -5 1050 55 1200 115 L1200 180 L0 180 Z" fill="#fcece0"/>
</svg>

<div class="card left peach" style="left:142px;top:946px">
  <div class="bag" role="img" aria-label="Kraft coffee bag with illustrated label"></div>
  <h3>PRODUCT NAME</h3>
  <p>Duis aute irure dolor in reprehenderit inptate velit esse cillum dolore eu fugiat nuriatur.</p>
  <span class="price">$56.78</span><span class="stars">☆☆☆☆☆</span>
  <a class="btn">SHOP NOW<span class="btn-icon"><svg width="14" height="13" viewBox="0 0 20 18"><path d="M1 2h3l2.5 9h10l2-7H5.5Z" fill="#111"/><circle cx="8" cy="15" r="2" fill="#111"/><circle cx="15" cy="15" r="2" fill="#111"/></svg></span></a>
</div>
<div class="card right" style="left:618px;top:946px">
  <div class="bag" role="img" aria-label="Kraft coffee bag with illustrated label"></div>
  <h3>PRODUCT NAME</h3>
  <p>Duis aute irure dolor in reprehenderit inptate velit esse cillum dolore eu fugiat nuriatur.</p>
  <span class="price">$56.78</span><span class="stars">☆☆☆☆☆</span>
  <a class="btn">SHOP NOW<span class="btn-icon"><svg width="14" height="13" viewBox="0 0 20 18"><path d="M1 2h3l2.5 9h10l2-7H5.5Z" fill="#111"/><circle cx="8" cy="15" r="2" fill="#111"/><circle cx="15" cy="15" r="2" fill="#111"/></svg></span></a>
</div>
<div class="card left" style="left:142px;top:1321px">
  <div class="bag" role="img" aria-label="Kraft coffee bag with illustrated label"></div>
  <h3>PRODUCT NAME</h3>
  <p>Duis aute irure dolor in reprehenderit inptate velit esse cillum dolore eu fugiat nuriatur.</p>
  <span class="price">$56.78</span><span class="stars">☆☆☆☆☆</span>
  <a class="btn">SHOP NOW<span class="btn-icon"><svg width="14" height="13" viewBox="0 0 20 18"><path d="M1 2h3l2.5 9h10l2-7H5.5Z" fill="#111"/><circle cx="8" cy="15" r="2" fill="#111"/><circle cx="15" cy="15" r="2" fill="#111"/></svg></span></a>
</div>
<div class="card right" style="left:618px;top:1321px">
  <div class="bag" role="img" aria-label="Kraft coffee bag with illustrated label"></div>
  <h3>PRODUCT NAME</h3>
  <p>Duis aute irure dolor in reprehenderit inptate velit esse cillum dolore eu fugiat nuriatur.</p>
  <span class="price">$56.78</span><span class="stars">☆☆☆☆☆</span>
  <a class="btn">SHOP NOW<span class="btn-icon"><svg width="14" height="13" viewBox="0 0 20 18"><path d="M1 2h3l2.5 9h10l2-7H5.5Z" fill="#111"/><circle cx="8" cy="15" r="2" fill="#111"/><circle cx="15" cy="15" r="2" fill="#111"/></svg></span></a>
</div>
<div class="abs medallion"><span></span></div>

<!-- ABOUT -->
<div class="abs about-bg" style="top:2160px;height:600px"></div>
<div class="abs coffee-photo" role="img" aria-label="Bowl of ground coffee with scattered roasted beans and a green leaf"></div>
<h2 class="abs display about-title">ABOUT US</h2>
<span class="rule" style="left:618px;top:2262px"></span>
<p class="abs about-text">Sed ut perspiciatis unde omnis iste natus error sit voluptatem accusantium doloremque laudantium, totam rem aperiam, eaque ipsa quae ab illo inventore veritatis et quasi architecto beatae vitae dicta sunt explicabo. Nemo enim ipsam voluptatem quia voluptas sit aspernatur aut odit aut fugit, sed quia consequuntur magni dolores eos qui ratione voluptatem sequi nesciunt.</p>
<a class="btn" style="left:618px;top:2498px;width:134px;height:39px;font-size:11px">READ MORE</a>
<svg class="abs" style="left:0;top:2570px" width="1200" height="200" viewBox="0 0 1200 200">
  <path d="M0 200 L0 160 C200 80 420 20 620 30 C850 40 1050 110 1200 150 L1200 200 Z" fill="#fff"/>
</svg>

<!-- BLOG -->
<h2 class="abs display blog-title">BLOG POSTS</h2>
<span class="rule" style="left:585px;top:2757px"></span>
<div class="abs meadow" role="img" aria-label="Misty mountain meadow with a resting saddled horse"></div>

<article class="post" style="left:144px;top:2810px">
  <div class="post-img" role="img" aria-label="Portafilter of ground coffee among roasted beans" style="background:linear-gradient(135deg,#6b4a33,#2f1d12)"></div>
  <span class="date">JAN 17,2025</span>
  <h4>UM QUIA DOLOR SIT AMETONSECTE</h4>
  <p>Sed ut perspiciatis unde omnis iste natus error sit voluptatem accusantium</p>
  <a>READ MORE</a>
</article>
<article class="post" style="left:457px;top:2810px;width:284px">
  <div class="post-img" role="img" aria-label="Hands holding freshly roasted coffee beans" style="background:linear-gradient(135deg,#c08a5e,#4a2a18)"></div>
  <span class="date" style="top:156px;background:var(--orange)">JAN 17,2025</span>
  <h4 style="margin-top:27px">UM QUIA DOLOR SIT AMETONSECTE</h4>
  <p>Sed ut perspiciatis unde omnis iste natus error sit voluptatem accusantis unde omnis iste natus error</p>
  <a>READ MORE</a>
</article>
<article class="post" style="left:760px;top:2810px">
  <div class="post-img" role="img" aria-label="Coffee plantation rows on a hillside" style="background:linear-gradient(180deg,#c9d3d0,#3e5a2e 40%,#1f3318)"></div>
  <span class="date">JAN 17,2025</span>
  <h4>UM QUIA DOLOR SIT AMETONSECTE</h4>
  <p>Sed ut perspiciatis unde omnis iste natus error sit voluptatem accusantium</p>
  <a>READ MORE</a>
</article>
<a class="btn" style="left:508px;top:3195px;width:183px;height:54px;font-size:13px">VIEW MORE BLOGS</a>

<!-- FOOTER -->
<div class="abs footer"></div>
<svg class="abs" style="left:0;top:3300px" width="1200" height="160" viewBox="0 0 1200 160">
  <path d="M0 70 C200 160 420 170 640 110 C860 50 1050 20 1200 40 L1200 160 L0 160 Z" fill="#3a1a10"/>
  <path d="M360 160 C500 150 600 120 700 85" fill="none" stroke="#d2601a" stroke-width="6" stroke-linecap="round"/>
</svg>
<div class="abs subscribe">
  <h5>SUBSCRIBE &amp; SAVE</h5>
  <div class="email">Enter Email</div>
  <a class="btn">SUBSCRIBE</a>
</div>

<div class="fcol" style="left:179px">
  <h6>CONTACT US</h6>
  <div class="contact-item"><svg width="16" height="14" viewBox="0 0 16 14" style="margin-top:3px"><path d="M1 2l4-1 6 2 4-1v11l-4 1-6-2-4 1Z" fill="#fff"/></svg><span>123,uptatem accusantium<br>doloremquelarc</span></div>
  <div class="contact-item" style="margin-top:18px;font-size:15px"><svg width="14" height="14" viewBox="0 0 14 14" style="margin-top:3px"><path d="M3 1l2.5 3-1.5 1.5a8 8 0 0 0 4.5 4.5L10 8.5 13 11l-1.5 2C6 13 1 8 1 2.5Z" fill="#fff"/></svg><span>+1 888 888 8888</span></div>
</div>
<div class="fcol" style="left:510px">
  <h6>MENUS</h6>
  <ul style="display:grid;grid-template-columns:110px 90px;line-height:0"><li>Home</li><li>Blog</li><li>About Us</li><li>Contact Us</li><li>Shop</li></ul>
</div>
<div class="fcol" style="left:842px">
  <h6>LINKS</h6>
  <ul><li>Customer inquiries</li><li>Shipping &amp; return policies</li><li>Wholesale &amp; bulk orders</li></ul>
</div>

<div class="abs bottom-line"></div>
<p class="abs legal">© 2025 Companyname.All Rights Reserved &nbsp;|&nbsp; Privacy Policy &nbsp;|&nbsp; Terms of Use</p>
<div class="abs cards"><span></span><span></span><span></span><span></span><span></span></div>
<div class="abs social"><span></span><span></span><span></span><span></span></div>

</body>
</html>
```